Security Consulting firm needs an ad design

We need a 3.375” x 4.875” ad design for our core services. The ad should include the company logo and the content from the first half of the attached sample JPG (Without the sentence under the title but including the description for the Plan - Design - Deploy - Manage and the titles ) as well as the following corporate information:
www.harrowfieldco.us
82 Marrow Ave. Suite 615, Pinecrest Hollow, NJ 07381
PHONE 888-412-6057 / EMAIL info@harrowfieldco.us
The design should incorporate the same blue color that is in our logo and the font Raleway. Also - please use the same icons that are in the sample JPG - they can also be extracted from the attached indesign file.
The ad is to be publish in print and digital issue.
Please provide with all source files as well as a hi-res PDF using press quality or similar PDF settings.
- Raleway

```html
<!DOCTYPE html>
<html lang="en">
<head>
<meta charset="utf-8">
<title>Harrowfield Consulting – Creating Secure Environments</title>
<link rel="stylesheet" href="https://fonts.googleapis.com/css2?family=Raleway:wght@300;400;500;600;700;800;900&display=swap">
<style>
  :root {
    --navy: #111a2b;
    --navy-deep: #0b1220;
    --brand-blue: #2f74b5;
    --sky-blue: #3d9be0;
    --panel: #e8f0f8;
    --ink: #4a4f57;
    --white: #ffffff;
    --divider: #c9d3de;
  }
  * { margin: 0; padding: 0; box-sizing: border-box; }
  html, body { width: 831px; height: 1200px; overflow: hidden; background: var(--white); }
  body { font-family: "Raleway", sans-serif; }

  .ad { position: relative; width: 831px; height: 1200px; overflow: hidden; background: var(--navy); }

  .hero { position: absolute; left: 0; top: 0; width: 831px; height: 541px;
    background: linear-gradient(100deg, var(--navy-deep) 0%, #18243a 45%, #2a3346 70%, #6a6468 100%); }
  .hero-photo { position: absolute; right: 0; top: 0; width: 330px; height: 541px;
    background: radial-gradient(ellipse at 62% 45%, #b9a49a 0%, #7a6c6c 35%, rgba(42,51,70,0) 75%); }

  .brand { position: absolute; left: 51px; top: 58px; display: flex; align-items: center; gap: 12px; }
  .brand-dot { width: 56px; height: 56px; border-radius: 50%; background: var(--brand-blue); }
  .brand-text { display: flex; flex-direction: column; }
  .brand-name { color: var(--white); font-weight: 700; font-size: 44px; line-height: 1; letter-spacing: -0.5px; }
  .brand-text .tag { color: var(--white); font-weight: 700; font-size: 13px; letter-spacing: 13.5px; margin-top: 6px; }

  .headline { position: absolute; left: 51px; top: 200px; }
  .headline .lead { display: block; color: var(--white); font-weight: 300; font-size: 62px; line-height: 1; }
  .headline .key { display: block; color: var(--sky-blue); font-weight: 900; font-size: 124px; line-height: 1; margin-top: -10px; letter-spacing: -1px; }
  .headline .tail { display: block; color: var(--sky-blue); font-weight: 800; font-size: 61px; line-height: 1; margin-top: -6px; letter-spacing: -0.5px; }

  .services { position: absolute; left: 0; top: 541px; width: 831px; height: 463px; background: var(--panel); }
  .services .rule { position: absolute; left: 416px; width: 3px; background: var(--divider); }

  .service { position: absolute; width: 380px; text-align: center; }
  .service .badge { position: absolute; left: 50%; width: 144px; height: 144px; margin-left: -72px; border-radius: 50%; background: var(--panel); }
  .service .icon { position: absolute; left: 50%; width: 114px; height: 114px; margin-left: -57px; border-radius: 50%; background: var(--white);
    box-shadow: 0 4px 8px rgba(20,40,70,0.25); display: flex; align-items: center; justify-content: center; }
  .service .icon svg { width: 64px; height: 64px; fill: var(--brand-blue); }
  .service h2 { color: var(--brand-blue); font-weight: 800; font-size: 33px; line-height: 1; }
  .service p { color: var(--ink); font-weight: 500; font-size: 22px; line-height: 26px; margin-top: 9px; }
  .service.top .text { padding-top: 146px; }
  .service.bottom .text { padding-top: 131px; }

  .band-dark { position: absolute; left: 0; top: 1004px; width: 831px; height: 13px; background: var(--navy); }
  .contact { position: absolute; left: 0; top: 1017px; width: 831px; height: 183px; background: var(--brand-blue); color: var(--white); }
  .contact .rule { position: absolute; left: 404px; top: 33px; width: 2px; height: 73px; background: rgba(255,255,255,0.25); }
  .phone { position: absolute; left: 74px; top: 32px; display: flex; align-items: center; gap: 10px; font-weight: 800; font-size: 36px; line-height: 1; }
  .email { position: absolute; left: 74px; top: 73px; display: flex; align-items: center; gap: 10px; font-weight: 500; font-size: 22px; line-height: 1; }
  .address { position: absolute; left: 440px; top: 40px; display: flex; gap: 10px; font-weight: 400; font-size: 22px; line-height: 29px; font-style: normal; }
  .contact svg { fill: var(--navy); flex: none; }
  .web { position: absolute; left: 0; top: 115px; width: 831px; text-align: center; font-weight: 800; font-size: 33px; letter-spacing: 3.5px; }
</style>
</head>
<body>
<main class="ad">
  <section class="hero">
    <div class="hero-photo" role="img" aria-label="Photo of a security operator wearing a headset in a dimly lit monitoring room"></div>

    <div class="brand">
      <span class="brand-dot"></span>
      <div class="brand-text">
        <span class="brand-name">harrowfield</span>
        <span class="tag">CONSULTING</span>
      </div>
    </div>

    <h1 class="headline">
      <span class="lead">CREATING</span>
      <span class="key">SECURE</span>
      <span class="tail">ENVIRONMENTS</span>
    </h1>
  </section>

  <section class="services">
    <span class="rule" style="top:41px;height:161px"></span>
    <span class="rule" style="top:270px;height:162px"></span>

    <article class="service top" style="left:37px;top:-72px">
      <span class="badge" style="top:0"></span>
      <span class="icon" style="top:15px">
        <svg viewBox="0 0 64 64" aria-hidden="true"><path d="M14 10h9a9 9 0 0 1 18 0h9a4 4 0 0 1 4 4v44a4 4 0 0 1-4 4H14a4 4 0 0 1-4-4V14a4 4 0 0 1 4-4zm2 6v40h32V16h-6v4H22v-4zm11-8v3h10V8a5 5 0 0 0-10 0zM19 25l2-2 3 3 5-5 2 2-7 7zm14 0h12v3H33zM19 36l2-2 3 3 5-5 2 2-7 7zm14 0h12v3H33zM19 47l2-2 3 3 5-5 2 2-7 7zm14 0h12v3H33z"/></svg>
      </span>
      <div class="text">
        <h2>PLAN</h2>
        <p>Security Assessment and<br>Planning Services</p>
      </div>
    </article>

    <article class="service top" style="left:418px;top:-72px">
      <span class="badge" style="top:0"></span>
      <span class="icon" style="top:15px">
        <svg viewBox="0 0 64 64" aria-hidden="true"><path d="M28 4h8l1 7 5 2 6-4 6 6-4 6 2 5 7 1v8l-7 1-1 3-6-6a16 16 0 1 0-10 14l4 4-2 1-1 7h-8l-1-7-5-2-6 4-6-6 4-6-2-5-7-1v-8l7-1 2-5-4-6 6-6 6 4 5-2zM22 22a12 12 0 0 1 16-2l-7 7 1 5 5 1 7-7a12 12 0 0 1-14 16l12 12a4 4 0 0 0 6-6L36 36z"/></svg>
      </span>
      <div class="text">
        <h2>DESIGN</h2>
        <p>Security Design and<br>Engineering</p>
      </div>
    </article>

    <article class="service bottom" style="left:35px;top:196px">
      <span class="icon" style="top:0">
        <svg viewBox="0 0 64 64" aria-hidden="true"><path d="M58 6c-14 0-24 6-31 16l-9 1-8 8 10 2 10 10 2 10 8-8 1-9c10-7 16-17 17-30zM42 16a5 5 0 1 1 0 10 5 5 0 0 1 0-10zM14 40c-4 2-7 8-7 17 9 0 15-3 17-7z"/></svg>
      </span>
      <div class="text">
        <h2>DEPLOY</h2>
        <p>Procurement and Project<br>Management Services</p>
      </div>
    </article>

    <article class="service bottom" style="left:416px;top:202px">
      <span class="icon" style="top:0">
        <svg viewBox="0 0 64 64" aria-hidden="true"><circle cx="32" cy="11" r="8"/><path d="M20 30a12 8 0 0 1 24 0v4H20z"/><path d="M12 34c4 8 12 10 20 10s16-2 20-10" fill="none" stroke="#2f74b5" stroke-width="3"/><circle cx="9" cy="34" r="5"/><circle cx="55" cy="34" r="5"/><circle cx="32" cy="54" r="5"/><path d="M30.5 44h3v6h-3z"/></svg>
      </span>
      <div class="text">
        <h2>MANAGE</h2>
        <p>Comprehensive Security<br>Program Management</p>
      </div>
    </article>
  </section>

  <div class="band-dark"></div>

  <footer class="contact">
    <span class="rule"></span>
    <div class="phone">
      <svg width="24" height="26" viewBox="0 0 24 24" aria-hidden="true"><path d="M6.6 10.8a15 15 0 0 0 6.6 6.6l2.2-2.2a1 1 0 0 1 1-.25 11.4 11.4 0 0 0 3.6.57 1 1 0 0 1 1 1V20a1 1 0 0 1-1 1A17 17 0 0 1 3 4a1 1 0 0 1 1-1h3.5a1 1 0 0 1 1 1c0 1.25.2 2.45.57 3.57a1 1 0 0 1-.25 1z"/></svg>
      <span>888-412-6057</span>
    </div>
    <div class="email">
      <svg width="26" height="18" viewBox="0 0 26 18" aria-hidden="true"><path d="M0 0h26v18H0zM2 3v1l11 7 11-7V3L13 10z"/></svg>
      <span>info@harrowfieldco.us</span>
    </div>
    <address class="address">
      <svg width="20" height="28" viewBox="0 0 20 28" aria-hidden="true"><path d="M10 0a10 10 0 0 1 10 10c0 7-10 18-10 18S0 17 0 10A10 10 0 0 1 10 0zm0 5a5 5 0 1 0 0 10 5 5 0 0 0 0-10z"/></svg>
      <span>82 Marrow Ave. Suite 615,<br>Pinecrest Hollow, NJ 07381</span>
    </address>
    <div class="web">www.harrowfieldco.us</div>
  </footer>
</main>
</body>
</html>
```